Letterhead and email signature block for school

We are a Remote School in the North West of Western Australia and I want to take our logo and use that to create a professional letter head and email signature block. A sample signature block is attached. For the Letterhead; The logo is also attached. I like the Orange and black combination of the logo, needs to include motto plus the following contact details;
PMB 4 KELLARUP WA
Phone: (08) 9170 3158
Fax: (08) 9170 3206
ABN: 41 287 519 302

The email signature block needs to have the following;
Dale Owen Wrenfield
Principal
Tern Ridge Hill RCS
Phone: (08) 9170 3158
Fax: (08) 9170 3206
Mobile: 0488 613 947
Email: Dale.Wrenfield@schoolnet-kx.org.au

Target Market(s)

Parents

Industry/Entity Type

Education

Contact Information for Business Card

Dale Owen Wrenfield
Principal
Tern Ridge Hill RCS
Phone: (08) 9170 3158
Fax: (08) 9170 3206
Mobile: 0488 613 947

Colors
f37122
000000

Requirements
Must have
• see breif

```html
<!DOCTYPE html>
<html lang="en">
<head>
<meta charset="utf-8">
<title>Tern Ridge Hill RCS – Letterhead</title>
<link rel="stylesheet" href="https://fonts.googleapis.com/css2?family=Roboto:wght@300;400;500&family=Mulish:wght@400&family=Noto+Serif:wght@400&display=swap">
<style>
  :root {
    --orange: #f37122;
    --orange-deep: #e2520f;
    --amber: #f9a03f;
    --black: #000000;
    --ink: #111111;
    --body-text: #8993a6;
    --paper: #ffffff;
    --paper-shade: #f1f1f1;
  }
  * { box-sizing: border-box; margin: 0; padding: 0; }
  html, body { width: 918px; height: 1200px; overflow: hidden; background: #ffffff; }
  .letterhead {
    position: relative;
    width: 918px;
    height: 1200px;
    overflow: hidden;
    background: linear-gradient(160deg, var(--paper) 55%, var(--paper-shade) 100%);
    font-family: "Roboto", Arial, sans-serif;
  }
  .corner { position: absolute; display: block; }
  .corner--top { top: 0; right: 0; width: 360px; height: 110px; }
  .corner--bottom { bottom: 0; left: 0; width: 520px; height: 150px; }

  .brand { position: absolute; left: 40px; top: 45px; width: 300px; text-align: center; }
  .brand__mark {
    width: 150px; height: 150px; border-radius: 50%;
    background: var(--orange); margin: 0 auto 38px;
  }
  .brand__name { font-size: 31px; font-weight: 400; color: var(--ink); line-height: 1; white-space: nowrap; }
  .brand__motto { margin-top: 9px; font-size: 12.5px; color: var(--ink); white-space: nowrap; }

  .contact { position: absolute; left: 606px; top: 137px; list-style: none; }
  .contact__item {
    display: flex; align-items: center; height: 39px;
    font-family: "Noto Serif", Georgia, serif; font-size: 17px; letter-spacing: 0.8px; color: var(--ink);
  }
  .contact__icon { width: 24px; height: 24px; margin-right: 20px; flex: none; }

  .letter { position: absolute; left: 49px; top: 362px; width: 815px; }
  .letter__headline { font-size: 32px; font-weight: 400; letter-spacing: 0.5px; color: var(--ink); margin-bottom: 30px; }
  .letter__para {
    font-family: "Mulish", Arial, sans-serif; font-size: 19px; line-height: 28.3px;
    letter-spacing: 1.2px; color: var(--body-text); margin-bottom: 28px;
  }

  .signature {
    position: absolute; left: 650px; top: 848px; width: 200px; height: 122px;
    background: radial-gradient(ellipse at 40% 50%, rgba(137,147,166,0.22), rgba(137,147,166,0) 70%);
  }
  .sign-off { position: absolute; right: 66px; top: 980px; text-align: right; }
  .sign-off__title { font-size: 17px; font-weight: 500; color: var(--ink); }
  .sign-off__role { font-size: 18px; font-weight: 300; color: var(--orange); letter-spacing: 0.5px; }
  .sign-off__web { font-size: 14px; color: var(--ink); letter-spacing: 0.4px; }
</style>
</head>
<body>
<main class="letterhead">

  <svg class="corner corner--top" viewBox="0 0 360 110" aria-hidden="true">
    <polygon points="140,0 360,0 360,110 330,110" fill="var(--amber)"/>
    <polygon points="190,0 360,0 360,84" fill="var(--orange)"/>
    <polygon points="250,0 360,0 360,50" fill="var(--black)"/>
  </svg>

  <div class="brand">
    <div class="brand__mark"></div>
    <p class="brand__name">Tern Ridge Hill RCS</p>
    <p class="brand__motto">Learning. Our People, Our Country, Our Tomorrow</p>
  </div>

  <ul class="contact">
    <li class="contact__item">
      <svg class="contact__icon" viewBox="0 0 24 24" aria-hidden="true"><path d="M12 2a7 7 0 0 0-7 7c0 5 7 13 7 13s7-8 7-13a7 7 0 0 0-7-7zm0 10a3 3 0 1 1 0-6 3 3 0 0 1 0 6z" fill="var(--orange)"/></svg>
      PMB 4 KELLARUP WA
    </li>
    <li class="contact__item">
      <svg class="contact__icon" viewBox="0 0 24 24" aria-hidden="true"><path d="M6.6 10.8a15 15 0 0 0 6.6 6.6l2.2-2.2c.3-.3.7-.4 1-.2 1.1.4 2.3.6 3.6.6.6 0 1 .4 1 1V20c0 .6-.4 1-1 1A17 17 0 0 1 3 4c0-.6.4-1 1-1h3.5c.6 0 1 .4 1 1 0 1.3.2 2.5.6 3.6.1.3 0 .7-.2 1z" fill="var(--orange)"/></svg>
      (08) 9170 3158
    </li>
    <li class="contact__item">
      <svg class="contact__icon" viewBox="0 0 24 24" aria-hidden="true"><rect x="2" y="6" width="5" height="15" rx="1" fill="var(--orange)"/><path d="M9 3h9v5h3v13H9z" fill="none" stroke="var(--orange)" stroke-width="2"/><rect x="12" y="12" width="2" height="2" fill="var(--orange)"/><rect x="16" y="12" width="2" height="2" fill="var(--orange)"/><rect x="12" y="16" width="2" height="2" fill="var(--orange)"/><rect x="16" y="16" width="2" height="2" fill="var(--orange)"/></svg>
      (08) 9170 3206
    </li>
    <li class="contact__item">
      <svg class="contact__icon" viewBox="0 0 24 24" aria-hidden="true"><circle cx="10" cy="10" r="7" fill="none" stroke="var(--orange)" stroke-width="2"/><path d="M3 10h14M10 3c3 3 3 11 0 14M10 3c-3 3-3 11 0 14" fill="none" stroke="var(--orange)" stroke-width="1.5"/><path d="M15 15l6 6" stroke="var(--orange)" stroke-width="3" stroke-linecap="round"/></svg>
      ABN: 41 287 519 302
    </li>
  </ul>

  <article class="letter">
    <h1 class="letter__headline">HEAD LINE</h1>
    <p class="letter__para">Lorem ipsum dolor sit amet, consectetur adipiscing elit. Fusce dignissim pretium consectetur. Curabitur tempor posuere massa in varius. Pellentesque viverra nibh eu vehicula mattis. Nullam porta facilisis justo, a feugiat dolor sodales sed. Vestibulum neque nisi, elementum tincidunt metus sit amet, egestas bibendum enim. Aenean a blandit elit, vel rutrum mi. Nunc dapibus turpis sed massa aliquet tincidunt.</p>
    <p class="letter__para">Pellentesque id neque ligula. Nullam posuere, ligula a mattis posuere, lacus nisl adipiscing nunc, eu congue justo est ut diam. Nam quam nibh, dignissim non consequat in, semper eget purus. Nulla arcu sapien, viverra vitae metus tempor, congue ornare diam.</p>
    <p class="letter__para">Pellentesque vel nibh tempus, ullamcorper tortor sed, bibendum augue. Phasellus sollicitudin justo et quam aliquam sollicitudin. Sed eget nibh mollis, mattis sem et, viverra nulla.</p>
  </article>

  <div class="signature" role="img" aria-label="Handwritten signature"></div>

  <div class="sign-off">
    <p class="sign-off__title">Designation</p>
    <p class="sign-off__role">lorem ipsum dolor sit</p>
    <p class="sign-off__web">www.ternridgehill.example</p>
  </div>

  <svg class="corner corner--bottom" viewBox="0 0 520 150" aria-hidden="true">
    <polygon points="0,0 520,150 0,150" fill="var(--amber)"/>
    <polygon points="0,40 380,150 0,150" fill="var(--orange)"/>
    <polygon points="0,80 240,150 0,150" fill="var(--black)"/>
  </svg>

</main>
</body>
</html>
```